New design for existing catalog pages

We want to update and improve our existing design. The existing products on the designs should be adopted. Also the prices, descriptions and article numbers.
It is important that we receive an Indesign file that we can adapt. Also replace the images and adjust texts and prices.

Target Market(s)

Older people with high incomes. More conservative people.

Industry/Entity Type

Münzen und Briefmarkenhandel

Requirements
Must have
• Noble, simple and timeless design that looks high quality.
Nice to have
• The expensive products should be presented accordingly
Should not have
• Don't look cheap. Not too many different and bright colors

```html
<!DOCTYPE html>
<html lang="de">
<head>
<meta charset="utf-8">
<title>Top Münz-Raritäten – Seite 13</title>
<link href="https://fonts.googleapis.com/css2?family=Playfair+Display:wght@400;500&family=Montserrat:wght@400;500;800;900&display=swap" rel="stylesheet">
<style>
  :root{
    --royal:#2121d8;
    --ink:#111;
    --text-grey:#555;
    --silver-hi:#f2f5f5;
    --silver-mid:#c9d1d1;
    --silver-low:#9aa6a6;
    --gold-hi:#f3df9a;
    --gold-mid:#d2ad4f;
    --gold-low:#9a7526;
    --paper:#fff;
  }
  *{box-sizing:border-box;margin:0;padding:0}
  html,body{width:848px;height:1200px;overflow:hidden;background:var(--paper)}
  body{position:relative;font-family:'Montserrat',sans-serif;color:var(--ink)}
  .page{position:absolute;inset:0;border:1px solid #222}
  .abs{position:absolute}

  .running-head{left:32px;width:784px;top:0;height:64px;border-bottom:1px solid var(--royal)}
  .running-head .tab{position:absolute;left:231px;width:322px;top:29px;height:35px;border:1px solid var(--royal);border-bottom:none;border-radius:14px 14px 0 0;background:var(--paper);
    display:flex;align-items:center;justify-content:center;font-size:22px;letter-spacing:.5px;color:var(--royal);padding-top:3px}

  .rule-double{left:32px;width:784px;height:4px;border-top:1px solid var(--royal);border-bottom:1px solid var(--royal)}
  .section-title{left:0;width:848px;text-align:center;font-family:'Playfair Display',serif;font-weight:500;font-size:34px;color:var(--royal);line-height:1}

  .coin{border-radius:50%;box-shadow:4px 8px 14px rgba(0,0,0,.28);
    background:radial-gradient(circle at 38% 32%,var(--gold-hi),var(--gold-mid) 55%,var(--gold-low) 100%)}
  .coin.pale{background:radial-gradient(circle at 38% 32%,#f7ecc4,#dcc589 60%,#a78d4d 100%)}

  .price-box{left:305px;width:238px;border-radius:16px;border:2px solid #8e9a9a;
    background:linear-gradient(180deg,var(--silver-hi) 0%,var(--silver-mid) 58%,#b9c3c3 58%,var(--silver-hi) 100%);
    box-shadow:3px 6px 10px rgba(0,0,0,.25);text-align:center}
  .price-box .price{font-weight:900;font-size:29px;letter-spacing:-.3px;line-height:1}
  .price-box .article{font-weight:800;font-size:19px;line-height:1}

  .spec-box{left:305px;width:238px;top:271px;height:104px;border-radius:16px;border:2px solid #8e9a9a;
    background:linear-gradient(180deg,var(--silver-hi) 0%,var(--silver-mid) 60%,#c2cbcb 60%,var(--silver-hi) 100%);
    box-shadow:3px 6px 10px rgba(0,0,0,.25);padding:7px 0 0 41px;overflow:hidden}
  .spec-box li{list-style:none;font-size:11.5px;line-height:17.8px;font-weight:500;white-space:nowrap}
  .spec-box li::before{content:"◈";margin-right:2px;font-size:10px}

  .desc{left:32px;width:784px;font-size:11.6px;line-height:15px;color:var(--text-grey);text-align:justify;text-align-last:center}

  .ribbon{left:312px;width:228px;height:68px}
  .ribbon text{font-family:'Montserrat',sans-serif;font-weight:900;font-size:17px;fill:#fff}

  .footer-rule{left:31px;width:786px;height:1px;background:var(--royal)}
  .ornament{left:332px;top:1118px;width:184px;height:36px;background:linear-gradient(90deg,#fff,#dfe0fb 30%,#dfe0fb 70%,#fff)}
  .page-number{left:0;width:848px;top:1162px;text-align:center;font-size:11px;color:var(--royal)}
  .footer-title{right:33px;top:1161px;font-size:12px;color:var(--royal);letter-spacing:.3px}
</style>
</head>
<body>
<div class="page">

  <header class="abs running-head"><div class="tab">TOP MÜNZ-RARITÄTEN</div></header>

  <!-- Angebot 1 -->
  <div class="abs rule-double" style="top:92px"></div>
  <h2 class="abs section-title" style="top:104px">20 Franken 1873, 3-Punkt - Probeprägung</h2>
  <div class="abs rule-double" style="top:147px"></div>

  <div class="abs coin" style="left:52px;top:171px;width:200px;height:200px" role="img" aria-label="Goldmünze 20 Franken 1873, Wertseite mit Eichenkranz"></div>
  <div class="abs coin" style="left:591px;top:171px;width:200px;height:200px" role="img" aria-label="Goldmünze 20 Franken 1873, Bildseite mit sitzender Helvetia"></div>

  <div class="abs price-box" style="top:168px;height:94px">
    <div class="price" style="margin-top:18px">9995,– CHF</div>
    <div class="article" style="margin-top:20px">7870.1873.01</div>
  </div>
  <ul class="abs spec-box">
    <li>Jahr 1873</li>
    <li>Gold – 900/1'000 Feinheit</li>
    <li>Gewicht 6,451 Gramm</li>
    <li>Durchmesser 21 mm</li>
    <li>Auflage: 1'000 Stück</li>
  </ul>

  <p class="abs desc" style="top:393px">1873 liess das Finanzdepartement vom bekannten Graveur Anton Berghof in seiner Prägestätte in Brüssel ein Stempelpaar und 1'000 Exemplare einer neuen Eidgenössischen Goldmünze anfertigen. Der oberste der drei Punkte beinhaltete das Münzzeichen des Graveurs und stellte einen Engelskopf dar, der jedoch bei oberflächlicher Betrachtung als Punkt wahrgenommen wird.</p>

  <!-- Angebot 2 -->
  <div class="abs rule-double" style="top:451px"></div>
  <h2 class="abs section-title" style="top:465px">Das 100 Franken Vreneli von 1925</h2>
  <div class="abs rule-double" style="top:508px"></div>

  <div class="abs coin pale" style="left:52px;top:526px;width:200px;height:200px" role="img" aria-label="Goldmünze 100 Franken 1925, Wertseite mit Strahlenkreuz"></div>
  <div class="abs coin pale" style="left:591px;top:526px;width:200px;height:200px" role="img" aria-label="Goldmünze 100 Franken 1925, Helvetiakopf"></div>

  <div class="abs price-box" style="top:606px;height:94px">
    <div class="price" style="margin-top:19px">25900,– CHF</div>
    <div class="article" style="margin-top:20px">7874.1925.08</div>
  </div>
  <svg class="abs ribbon" style="top:553px" viewBox="0 0 228 68" aria-hidden="true">
    <polygon points="0,18 26,12 26,48 10,52" fill="#1a1ab8"/>
    <polygon points="228,10 202,6 202,40 218,44" fill="#1a1ab8"/>
    <polygon points="22,14 204,0 204,38 22,56" fill="var(--royal)"/>
    <polygon points="26,18 200,4 200,34 26,52" fill="none" stroke="#fff" stroke-width="1" stroke-dasharray="1.5 2"/>
    <text x="113" y="38" text-anchor="middle" transform="rotate(-4.5 113 32)">TOP - RARITÄT</text>
  </svg>

  <p class="abs desc" style="top:742px">1925, 100 Fr. Gold-Vreneli, bis unzirkuliert, mit Stempelglanz, Top-Erhaltung, Durchmesser: 35mm, Motiv: Helvetiakopf (Vreneli), Entwurf: Henri Marcel Duvoisin, Neuchâtel, Münzzeichen B, Auflage: 5'000</p>

  <!-- Angebot 3 -->
  <div class="abs rule-double" style="top:784px"></div>
  <h2 class="abs section-title" style="top:797px">Das 100 Franken Vreneli von 1925</h2>
  <div class="abs rule-double" style="top:840px"></div>

  <div class="abs coin" style="left:52px;top:856px;width:200px;height:200px" role="img" aria-label="Goldmünze 100 Franken 1925 in Stempelglanz, Wertseite"></div>
  <div class="abs coin pale" style="left:591px;top:856px;width:200px;height:200px" role="img" aria-label="Goldmünze 100 Franken 1925 in Stempelglanz, Helvetiakopf"></div>

  <div class="abs price-box" style="top:933px;height:94px">
    <div class="price" style="margin-top:19px">25900,– CHF</div>
    <div class="article" style="margin-top:20px">7874.1925.07</div>
  </div>
  <svg class="abs ribbon" style="top:880px" viewBox="0 0 228 68" aria-hidden="true">
    <polygon points="0,18 26,12 26,48 10,52" fill="#1a1ab8"/>
    <polygon points="228,10 202,6 202,40 218,44" fill="#1a1ab8"/>
    <polygon points="22,14 204,0 204,38 22,56" fill="var(--royal)"/>
    <polygon points="26,18 200,4 200,34 26,52" fill="none" stroke="#fff" stroke-width="1" stroke-dasharray="1.5 2"/>
    <text x="113" y="38" text-anchor="middle" transform="rotate(-4.5 113 32)">TOP - QUALITÄT</text>
  </svg>

  <p class="abs desc" style="top:1072px">1925, 100 Fr. Gold-Vreneli, fast FDC, Top-Erhaltung, Durchmesser: 35mm, Motiv: Helvetiakopf (Vreneli), Entwurf: Henri Marcel Duvoisin, Neuchâtel, Münzzeichen B, Auflage: 5'000</p>

  <!-- Fusszeile -->
  <div class="abs footer-rule" style="top:1128px"></div>
  <div class="abs footer-rule" style="top:1136px"></div>
  <div class="abs footer-rule" style="top:1144px"></div>
  <div class="abs ornament" role="img" aria-label="Rautenornament"></div>
  <div class="abs page-number">13</div>
  <div class="abs footer-title">TOP MÜNZ-RARITÄTEN</div>
</div>
</body>
</html>
```